Stationery Design Project for Marketing Consultancy

I have started a new consultancy business and require the following elements to be designed using existing logo:
• Business card
• Letterhead
• Envelope (DL, C4, C5)
• Microsoft word template for report writing
• A4 Presentation Folder
• Powerpoint template
COPY FOR FRONT AND BACK OF BUSINESS CARD
logo
'Measurable Marketing. Epic Results' slogan (but no need to use existing lockup with logo)
name, B Bus. Mktg, Grad Dip Digital Mktg, CPM (post nominal abbreviations in smaller font)
mobile: 04XX-XXX-XXX (I will give details to the winner to add)
website: www.tolvarin.com.au
email: info@tolvarin.com.au
COPY FOR LETTERHEAD
Logo
Company Name
Please, submit your designs that include business card, letterhead and envelope. Once selected the winner will be asked to complete the project by creating the rest of the artwork.
FINAL FILES
Print ready files to be supplied as well as Indesign files so that minor amends can be made if necessary in future.
• Layered vectors in EPS & PDF
• Screen quality JPEG & PNGs
ABOUT THE BUSINESS: TOLVARIN
I work with clients to understand their business challenges, developing and executing measurable marketing strategies tied to key business metrics. Services include:
Services include:
• Business planning and business development
• Marketing and brand strategy
• Insight-driven integrated campaigns
• Loyalty programs and retention marketing
• Marketing automation
• Direct marketing (traditional and digital)
• Content strategy and development
Hi everyone,
Target Market(s)
Corporate decision makers (heads of marketing, general managers etc) and small to medium sized business owners. Predominately male aged 35+
Industry/Entity Type
Marketing
Requirements
Must have
- BRAND PERSONALITY
The successful design will communicate brand personality. I am a professional, results-driven entrepreneur, but want to show off my creative flair.
MEMORABILITY
Looking for a unique and eye-catching design. Am considering special printing effects (die cuts, letterpress, interactive elements, embossing, foiling etc) or a striking minimalist approach.
Nice to have
- I have a mission that could be incorporated on reverse if room -
Turning insights into actions & passion into profit.
Should not have
- Use of pink or green.

```html
<!DOCTYPE html>
<html lang="en">
<head>
<meta charset="utf-8">
<title>Tolvarin Stationery</title>
<link rel="stylesheet" href="https://fonts.googleapis.com/css2?family=Ubuntu:wght@500;700&family=Open+Sans:wght@400;700&display=swap">
<style>
  :root {
    --backdrop: #d6d6d8;
    --ink: #0a0a0a;
    --paper: #ffffff;
    --reverse: #ffffff;
    --shadow: rgba(0,0,0,0.35);
  }
  * { margin: 0; padding: 0; box-sizing: border-box; }
  html, body { width: 1200px; height: 1017px; overflow: hidden; }
  body {
    position: relative;
    background: var(--backdrop);
    font-family: "Open Sans", Arial, sans-serif;
    color: var(--ink);
  }
  .piece {
    position: absolute;
    background: var(--paper);
    box-shadow: 3px 4px 6px var(--shadow);
    overflow: hidden;
  }
  .band { position: absolute; top: 0; left: 0; bottom: 0; background: var(--ink); }
  .wordmark {
    position: absolute;
    font-family: "Ubuntu", Arial, sans-serif;
    font-weight: 700;
    color: var(--reverse);
    letter-spacing: 0.02em;
    white-space: nowrap;
    line-height: 1;
  }
  .contact { position: absolute; line-height: 1.35; white-space: nowrap; }
  .contact .name { font-weight: 700; }
  .web { position: absolute; font-weight: 700; white-space: nowrap; line-height: 1; }

  /* Business card front */
  .card-front { left: 218px; top: 172px; width: 126px; height: 86px; background: var(--ink); }
  .card-front .wordmark { left: 0; right: 0; top: 52px; text-align: center; font-size: 12px; }

  /* Business card back */
  .card-back { left: 362px; top: 175px; width: 127px; height: 85px; background: var(--ink); }
  .card-back .wordmark { right: 8px; top: 17px; font-size: 6px; }
  .card-back .contact { left: 26px; top: 28px; font-size: 4.6px; color: var(--reverse); }
  .card-back .contact .name { font-size: 6px; margin-bottom: 4px; }

  /* DL envelope */
  .dl { left: 612px; top: 120px; width: 372px; height: 178px; }
  .dl .band { width: 150px; }
  .dl .wordmark { left: 14px; top: 155px; font-size: 11px; }
  .dl .contact { left: 202px; top: 143px; font-size: 5px; }
  .dl .contact .name { font-size: 6px; }
  .dl .web { right: 18px; top: 164px; font-size: 5px; font-weight: 400; }

  /* Letterhead */
  .letterhead { left: 188px; top: 326px; width: 348px; height: 469px; }
  .letterhead .band { width: 66px; }
  .letterhead .wordmark { left: 6px; top: 443px; font-size: 10px; }
  .letterhead .contact { left: 135px; top: 434px; font-size: 5.6px; }
  .letterhead .contact .name { font-size: 6.4px; }
  .letterhead .web { right: 17px; top: 453px; font-size: 5.6px; }

  /* C4 envelope */
  .c4 { left: 606px; top: 326px; width: 384px; height: 601px; background: transparent; box-shadow: none; overflow: visible; }
  .c4 .body {
    position: absolute; left: 0; top: 110px; width: 384px; height: 491px;
    background: var(--paper); box-shadow: 3px 4px 6px var(--shadow); overflow: hidden;
  }
  .c4 .body .band { width: 131px; }
  .c4 .body .wordmark { left: 0; width: 131px; text-align: center; top: 440px; font-size: 22px; }
  .c4 .body .web { left: 0; width: 131px; text-align: center; top: 468px; font-size: 5.6px; color: var(--reverse); }
  .c4 .flap { position: absolute; left: 0; top: 0; width: 384px; height: 112px; }
  .c4 .flap svg { display: block; }
  .c4 .flap .flap-shape { fill: var(--ink); }
  .c4 .flap .notch-line { fill: none; stroke: var(--reverse); stroke-width: 0.8; }
  .c4 .flap .notch-fill { fill: var(--reverse); }
  .c4 .flap .wordmark { left: 0; right: 0; top: 66px; text-align: center; font-size: 22px; }
</style>
</head>
<body>
  <section class="piece card-front" aria-label="Business card front">
    <div class="wordmark">TOLVARIN</div>
  </section>

  <section class="piece card-back" aria-label="Business card back">
    <div class="wordmark">TOLVARIN</div>
    <div class="contact">
      <div class="name">Company Name</div>
      <div>M: xxx xxx xxxx</div>
      <div>E: info@tolvarin.com.au</div>
      <div class="name">www.tolvarin.com.au</div>
    </div>
  </section>

  <section class="piece dl" aria-label="DL envelope">
    <div class="band"></div>
    <div class="wordmark">TOLVARIN</div>
    <div class="contact">
      <div class="name">Company Name</div>
      <div>M: xxx xxx xxxx</div>
      <div>E: info@tolvarin.com.au</div>
    </div>
    <div class="web">www.tolvarin.com.au</div>
  </section>

  <section class="piece letterhead" aria-label="Letterhead">
    <div class="band"></div>
    <div class="wordmark">TOLVARIN</div>
    <div class="contact">
      <div class="name">Company Name</div>
      <div>M: xxx xxx xxxx</div>
      <div>E: info@tolvarin.com.au</div>
    </div>
    <div class="web">www.tolvarin.com.au</div>
  </section>

  <section class="piece c4" aria-label="C4 envelope">
    <div class="body">
      <div class="band"></div>
      <div class="wordmark">TOLVARIN</div>
      <div class="web">www.tolvarin.com.au</div>
    </div>
    <div class="flap">
      <svg width="384" height="112" viewBox="0 0 384 112" aria-hidden="true">
        <path class="flap-shape" d="M6 0 H378 L384 70 A18 18 0 0 0 384 110 L384 112 H0 L0 110 A18 18 0 0 0 0 70 Z"/>
        <path class="notch-line" d="M0 72 A16 16 0 0 1 0 110"/>
        <path class="notch-fill" d="M384 72 A16 16 0 0 0 384 110"/>
      </svg>
      <div class="wordmark">TOLVARIN</div>
    </div>
  </section>
</body>
</html>
```